Flyer-Design für Musikverein - Jugendkapelle
Zielgruppe
Musikverein Kolmsried
Unsere Zielgruppe sind Kinder und Jugendliche, die ein Instrument erlernen wollen.
Der Einstieg der jüngsten geht in einem Alter ab ca. 8 Jahren los. Die meisten neuen Musiker steigen zwischen 10 - 14 Jahren ein.
Der Flyer soll aber auch geeignet sein um an Grund- und weiterführenden Schulen ausgelegt werden zu können um Musiker für die Jugendkapelle zu gewinnen. Dementsprechend frisch und interessant soll der Flyer gestaltet sein.
Aufgabenstellung
Es soll ansprechend sein für Jugendliche, frisch, fröhlich und soll das Interesse der jugendlichen mit dem Design wecken.
Es soll die Jugendlichkeit, die Blasmusik und das Vereinsleben miteinander verbinden, sowie die Vorteile und der Spaß an der Musik (Instrument erlernen, Spaß am Musizieren, neue Freunde und Kameradschaft und auch Freizeitaktivitäten) miteinander darstellen.

```html
<!DOCTYPE html>
<html lang="de">
<head>
<meta charset="utf-8">
<title>Musikverein Kolmsried – Mitmachen</title>
<link rel="stylesheet" href="https://fonts.googleapis.com/css2?family=Lobster&family=Source+Sans+3:wght@400;700&display=swap">
<style>
  :root {
    --ink: #141414;
    --paper: #ffffff;
    --red: #e2231a;
    --sky-top: #d9dde1;
    --sky-mid: #f4f5f6;
    --sky-low: #cfd5da;
  }
  html, body {
    margin: 0;
    padding: 0;
    overflow: hidden;
  }
  .flyer {
    position: relative;
    width: 1200px;
    height: 560px;
    overflow: hidden;
    font-family: "Source Sans 3", sans-serif;
    color: var(--ink);
  }
  .sky-backdrop {
    position: absolute;
    inset: 0;
    background:
      radial-gradient(ellipse at 30% 30%, var(--sky-mid) 0%, transparent 60%),
      radial-gradient(ellipse at 75% 70%, #eef0f2 0%, transparent 55%),
      linear-gradient(180deg, var(--sky-top) 0%, var(--sky-mid) 45%, var(--sky-low) 100%);
  }
  .headline {
    position: absolute;
    top: 10px;
    left: 0;
    width: 100%;
    margin: 0;
    text-align: center;
    font-family: "Lobster", cursive;
    font-weight: 400;
    font-size: 52px;
    line-height: 1.2;
  }
  .info-card {
    position: absolute;
    top: 106px;
    width: 486px;
    height: 353px;
    background: var(--paper);
    box-shadow: 0 6px 14px rgba(0, 0, 0, 0.28);
    box-sizing: border-box;
    padding: 10px 10px 0 10px;
    font-size: 23px;
    line-height: 34px;
  }
  .info-card--offer {
    left: 102px;
  }
  .info-card--instruments {
    left: 612px;
  }
  .card-lead {
    margin: 0;
    font-weight: 700;
    font-size: 23px;
    line-height: 33px;
  }
  .card-subhead {
    margin: 32px 0 0;
    font-weight: 700;
    font-size: 23px;
    line-height: 34px;
  }
  .bullet-list {
    list-style: none;
    margin: 0;
    padding: 0;
  }
  .bullet-list li {
    position: relative;
    padding-left: 18px;
  }
  .bullet-list li::before {
    content: "";
    position: absolute;
    left: 2px;
    top: 14px;
    width: 7px;
    height: 7px;
    border-radius: 50%;
    background: var(--ink);
  }
  .bullet-list--services {
    margin-left: 54px;
  }
  .bullet-list--instruments {
    margin: 32px 0 0 63px;
  }
  .start-note {
    margin: 24px 0 0;
  }
  .brush-stroke {
    position: absolute;
    left: 909px;
    top: 335px;
    width: 285px;
    height: 108px;
  }
  .web-address {
    position: absolute;
    left: 0;
    top: 468px;
    width: 100%;
    margin: 0;
    text-align: center;
    font-family: "Lobster", cursive;
    font-size: 62px;
    line-height: 1.2;
    color: var(--red);
  }
</style>
</head>
<body>
  <main class="flyer">
    <div class="sky-backdrop" role="img" aria-label="Heller Wolkenhimmel mit großen schwarzen Notenzeichen und Violinschlüssel als Dekoration"></div>

    <h1 class="headline">Hast Du Lust &amp; Zeit bei uns mitzumachen?</h1>

    <section class="info-card info-card--offer">
      <p class="card-lead">Wir bieten qualifizierten Musik-<br>unterricht für Kinder, Jugendliche und<br>Erwachsene an:</p>
      <h2 class="card-subhead">Unsere Leistungen:</h2>
      <ul class="bullet-list bullet-list--services">
        <li>Einzelunterricht</li>
        <li>Lehrkräfte mit Musikausbildung und<br>langjähriger pädagogischer Erfahrung</li>
      </ul>
      <p class="start-note">Unterrichtsbeginn immer am Monatsanfang.</p>
    </section>

    <section class="info-card info-card--instruments">
      <p class="card-lead">Folgende Musikinstrumente kannst Du<br>bei uns lernen:</p>
      <ul class="bullet-list bullet-list--instruments">
        <li>Trompete / Flügelhorn</li>
        <li>Tuba</li>
        <li>Tenorhorn / Bariton / Posaune</li>
        <li>Waldhorn</li>
        <li>Klarinette / Saxophon</li>
        <li>Querflöte</li>
      </ul>
    </section>

    <div class="brush-stroke" role="img" aria-label="Roter Farbfleck als Schmuckelement">
      <svg viewBox="0 0 285 108" width="285" height="108" aria-hidden="true">
        <rect x="30" y="14" width="255" height="86" rx="43" fill="#e2231a"/>
      </svg>
    </div>

    <p class="web-address">www.kolmsried-musikverein.de</p>
  </main>
</body>
</html>
```